Schriftdesign für Shop-Header Bild (Schmuckhandel) / Online-Marketing Material
Wir verkaufen Schmuck im Onlineshop mit Herz
Wir benötigen den vorgegebenen Text in schöner Form, Farbe und Größe harmonisch eingefügt, in unserem Bild.
Folgender Text soll sich schick ins Bild einfügen oder in 3-D vielleicht in Schriftfarbe gold hervorheben:
Mit ganzem Herzen für Sie da!
Ihr Online -Juwelier mit Herz
Siehe auch unser altes Bild mit Text, im Shop, wie es nicht aussehen sollte: www.sonnenflocke.de

```html
<!DOCTYPE html>
<html lang="de">
<head>
<meta charset="utf-8">
<title>Shop-Header – Mit ganzem Herzen für Sie da!</title>
<link href="https://fonts.googleapis.com/css2?family=Allura&family=Oswald:wght@200;300&display=swap" rel="stylesheet">
<style>
  :root {
    --canvas: #ffffff;
    --gold-band: #a89676;
    --gold-band-dark: #8f7e60;
    --rose-light: #c9a39a;
    --rose-mid: #9a6e66;
    --mauve: #6f4d47;
    --umber: #4a2e29;
    --night: #1c0f0d;
    --type-white: #ffffff;
    --type-rose: #f1d9d2;
    --type-soft: #ece3df;
  }
  html, body {
    margin: 0;
    width: 1200px;
    height: 1200px;
    overflow: hidden;
    background: var(--canvas);
  }
  .canvas {
    position: relative;
    width: 1200px;
    height: 1200px;
  }
  .header-banner {
    position: absolute;
    left: 0;
    top: 450px;
    width: 1200px;
    height: 300px;
    overflow: hidden;
  }
  .gold-band {
    position: absolute;
    left: 0; top: 0;
    width: 100%;
    height: 22px;
    background: linear-gradient(to bottom, var(--gold-band) 70%, var(--gold-band-dark));
  }
  .photo-area {
    position: absolute;
    left: 0; top: 22px;
    width: 100%;
    height: 278px;
    background:
      radial-gradient(ellipse 40% 70% at 30% 45%, rgba(214,176,140,0.35), transparent 70%),
      linear-gradient(100deg, var(--rose-light) 0%, var(--rose-mid) 30%, var(--mauve) 55%, var(--umber) 80%, #7a5a58 100%);
  }
  .tagline-strip {
    position: absolute;
    left: 0; bottom: 0;
    width: 100%;
    height: 90px;
    background: linear-gradient(to bottom, rgba(28,15,13,0) 0%, var(--night) 38%, var(--night) 100%);
  }
  .headline-top {
    position: absolute;
    right: 263px;
    top: 48px;
    margin: 0;
    font-family: "Oswald", "Arial Narrow", sans-serif;
    font-weight: 200;
    font-size: 42px;
    line-height: 1;
    color: var(--type-rose);
    letter-spacing: -0.5px;
    z-index: 1;
  }
  .headline-script {
    position: absolute;
    left: 600px;
    top: 58px;
    margin: 0;
    font-family: "Allura", cursive;
    font-weight: 400;
    font-size: 116px;
    line-height: 1;
    color: var(--type-white);
    z-index: 2;
  }
  .headline-bottom {
    position: absolute;
    left: 646px;
    top: 156px;
    margin: 0;
    font-family: "Oswald", "Arial Narrow", sans-serif;
    font-weight: 200;
    font-size: 60px;
    line-height: 1;
    color: var(--type-rose);
    letter-spacing: -0.5px;
  }
  .tagline {
    position: absolute;
    left: 0;
    width: 100%;
    top: 254px;
    margin: 0;
    text-align: center;
    font-family: "Oswald", "Arial Narrow", sans-serif;
    font-weight: 300;
    font-size: 17px;
    line-height: 1;
    letter-spacing: 8px;
    text-indent: 8px;
    color: var(--type-soft);
  }
</style>
</head>
<body>
  <main class="canvas">
    <section class="header-banner">
      <div class="gold-band"></div>
      <div class="photo-area" role="img" aria-label="Goldene Kette mit Herzanhänger auf rosafarbenem Seidenstoff"></div>
      <div class="tagline-strip"></div>
      <p class="headline-top">MIT GANZEM</p>
      <h1 class="headline-script">Herzen</h1>
      <p class="headline-bottom">für Sie da!</p>
      <p class="tagline">IHR ONLINE-JUWELIER MIT HERZ</p>
    </section>
  </main>
</body>
</html>
```